RESIDENTIAL CONSTRUCTION

We are a company that specializes in building custom residential homes, the design should also emphasize that quality and service is our priority.

Industry/Entity Type

Construction Company

Contact Information for Business Card

Contact Person: Marcus Lindqvist
Company Address: 273 West Alder Ave San Jose , Ca 95380
Phone Number : 408-731-2946
Email Address: Stoneridgehomes517@mailvista.net

Font styles to use
Sans Serif

Colors
ec1f27

Requirements
Must have
• CSLB # 7362015
Nice to have
• needs to have same color as logo i uploaded, we will be printing these on a clear plastic card.

```html
<!DOCTYPE html>
<html lang="en">
<head>
<meta charset="utf-8">
<title>Stoneridge Homes – Business Card</title>
<link rel="stylesheet" href="https://fonts.googleapis.com/css2?family=Roboto:wght@400;700;900&display=swap">
<style>
  :root {
    --brand-red: #c41e2f;
    --card-white: #ffffff;
    --text-grey: #6b6b6b;
    --band-light: #d9d9d9;
    --band-dark: #9a9a9a;
    --page-bg: #ecebe8;
  }
  * { box-sizing: border-box; margin: 0; padding: 0; }
  html, body {
    width: 1200px; height: 950px; overflow: hidden;
    background: var(--page-bg);
    font-family: "Roboto", Arial, sans-serif;
  }
  .sheet {
    position: relative; width: 1200px; height: 950px;
    display: flex; justify-content: center; align-items: center; gap: 80px;
  }
  .card {
    position: relative; width: 434px; height: 760px;
    box-shadow: 0 6px 18px rgba(0,0,0,0.18);
  }
  .card--back { background: var(--brand-red); }
  .card--front { background: var(--card-white); overflow: hidden; }

  .brand {
    position: absolute; top: 118px; left: 0; right: 0;
    display: flex; justify-content: center; align-items: center; gap: 12px;
  }
  .brand__mark { width: 34px; height: 34px; background: var(--brand-red); }
  .brand__name {
    color: var(--brand-red); font-weight: 900; font-size: 34px;
    letter-spacing: 0.5px; text-transform: uppercase; line-height: 1;
  }

  .contact {
    position: absolute; top: 408px; left: 0; right: 0;
    text-align: center; color: var(--text-grey);
    font-size: 18px; line-height: 27px;
  }
  .contact__name {
    color: var(--brand-red); font-weight: 700; font-size: 23px;
    text-transform: uppercase; letter-spacing: 0.5px; margin-bottom: 10px;
  }
  .contact__label { color: var(--brand-red); font-weight: 700; }

  .measure-band {
    position: absolute; left: 0; right: 0; bottom: 0; height: 42px;
    background: linear-gradient(to bottom, var(--band-light), var(--band-dark));
  }
</style>
</head>
<body>
  <main class="sheet">
    <section class="card card--front">
      <div class="brand">
        <span class="brand__mark"></span>
        <span class="brand__name">Stoneridge Homes</span>
      </div>
      <div class="contact">
        <p class="contact__name">Marcus Lindqvist</p>
        <p>273 West Alder Ave San Jose Ca 95380</p>
        <p>CSLB # 7362015</p>
        <p><span class="contact__label">P:</span> 408-731-2946</p>
        <p><span class="contact__label">E:</span> Stoneridgehomes517@mailvista.net</p>
      </div>
      <div class="measure-band" role="img" aria-label="Decorative tape-measure ruler edge along the bottom of the card"></div>
    </section>
    <section class="card card--back"></section>
  </main>
</body>
</html>
```